Investment company needing business card

We are wanting a business card which looks sharp and easy on the eye. We are thinking of having a business card with the logo embossed on it, to really make it stand out. We will only have a small amount of information of the business card, person's name, position, email address and phone number

Contact Information for Business Card

Danielle Frost
Executive Assistant
+64 21 473 5162
danielf@harwickpartners.co.nz

Requirements
Must have
• Embossed logo
Should not have
• Not to be busy

```html
<!DOCTYPE html>
<html lang="en">
<head>
<meta charset="UTF-8">
<title>Harwick Partners – Business Card</title>
<link href="https://fonts.googleapis.com/css2?family=Roboto:wght@400&family=Roboto+Condensed:wght@400;700&display=swap" rel="stylesheet">
<style>
  :root {
    --backdrop: #e9e8e4;
    --card: #f4f4f2;
    --brand-green: #27a35a;
    --ink-grey: #5a5b5d;
    --ink-dark: #3c3d3f;
    --mark-grey: #6a6b6d;
  }
  * { margin: 0; padding: 0; box-sizing: border-box; }
  html, body {
    width: 1200px;
    height: 761px;
    overflow: hidden;
    background: var(--backdrop);
  }
  .card {
    position: absolute;
    left: 110px;
    top: 100px;
    width: 980px;
    height: 560px;
    background: var(--card);
    box-shadow: 0 2px 6px rgba(0,0,0,0.08);
  }
  .identity {
    position: absolute;
    left: 94px;
    top: 118px;
    font-family: "Roboto Condensed", sans-serif;
    text-transform: uppercase;
  }
  .identity .name {
    color: var(--brand-green);
    font-weight: 700;
    font-size: 32px;
    line-height: 1.05;
    letter-spacing: 0.2px;
  }
  .identity .role {
    color: var(--ink-grey);
    font-weight: 400;
    font-size: 25px;
    line-height: 1.2;
  }
  .contact {
    position: absolute;
    right: 91px;
    top: 128px;
    text-align: right;
    font-family: "Roboto", sans-serif;
    font-size: 21px;
    line-height: 30px;
    color: var(--ink-dark);
    list-style: none;
  }
  .brand {
    position: absolute;
    right: 104px;
    top: 404px;
    display: flex;
    align-items: center;
    gap: 16px;
  }
  .brand .mark {
    width: 62px;
    height: 62px;
    background: var(--mark-grey);
  }
  .brand .wordmark {
    font-family: "Roboto Condensed", sans-serif;
    font-weight: 700;
    font-size: 42px;
    letter-spacing: 1px;
    text-transform: uppercase;
    color: var(--brand-green);
  }
</style>
</head>
<body>
  <div class="card">
    <div class="identity">
      <p class="name">Danielle Frost</p>
      <p class="role">Executive Assistant</p>
    </div>
    <ul class="contact">
      <li>+64 21 473 5162</li>
      <li>danielf@harwickpartners.co.nz</li>
      <li>www.harwickpartners.co.nz</li>
    </ul>
    <div class="brand">
      <span class="mark"></span>
      <span class="wordmark">Harwick Partners</span>
    </div>
  </div>
</body>
</html>
```